STICKER DESIGN required for packaging. UK START UP TEA BUSINESS

We are looking for a design for a sticker that will be applied to packaging for our teas! We are a new start up Tea business based in the UK called 'BrookLeafs'
Selling quality loose leaf tea and teabags via our online shop and also face to face at farmers markets / food shows and eventually in our own tea emporium. We will be marketing our teas to hotels, cafes, delis etc. too
We carry every day teas eg. breakfast blends and also speciality and rare teas to offer customers the chance to try something new. Tea as a treat / ritual / indulgence / healthy lifestyle choice / modern
The design will initially be printed on vinyl stickers and then applied to the tea packaging (pouch bags in matte black and matte silver), in the future the design may be printed direct onto our packaging. The sticker design will need to be scalable as the size of the pouch bag varies dependant on the tea.
The sticker we have in mind is a leaf shape (sketch attached)
colour green to match our logo
It will include our logo (files attached)
Text to be included on the sticker is
- www.brookleafs.co.uk
- Welmoor, England
- The tea type eg. Green
It will need to complement both black and silver pouches that we are using to package our teas (see attached image of our pouches)
Colours - green leaf, see our corporate colours (green & orange) on our logo files attached. We also like silver and black.
Font - nothing to swirly, must be easy to read on the packaging
once a sticker design is agreed for the initial tea type (Green) we will require additional files for each tea type that we stock. Just the tea type (Green) to be updated - the rest of the design to stay the same. The tea types we stock are listed below
Green
Black
Oolong
White
Herbal
Blended
Happy to answer any questions and aim to give feedback daily! Thank you for your interest
Best regards

```html
<!DOCTYPE html>
<html lang="en">
<head>
<meta charset="utf-8">
<title>BrookLeafs – Green Tea Sticker</title>
<link href="https://fonts.googleapis.com/css2?family=Questrial&family=Didact+Gothic&display=swap" rel="stylesheet">
<style>
  :root {
    --page: #e8e6e2;
    --leaf: #0c0c0c;
    --green: #8dc63f;
    --orange: #f7941d;
  }
  html, body {
    margin: 0;
    padding: 0;
    width: 1200px;
    height: 1194px;
    overflow: hidden;
    background: var(--page);
  }
  .sticker {
    display: block;
    width: 1200px;
    height: 1194px;
  }
  .leaf-body, .leaf-stem { fill: var(--leaf); }
  .guide { fill: none; stroke: none; }
  .brand-name {
    font-family: "Questrial", sans-serif;
    font-size: 64px;
    fill: var(--orange);
  }
  .brand-tagline {
    font-family: "Didact Gothic", sans-serif;
    font-size: 19px;
    letter-spacing: 1.5px;
    fill: var(--green);
  }
  .tea-type {
    font-family: "Questrial", sans-serif;
    font-size: 52px;
    fill: var(--green);
  }
  .rule { stroke: var(--orange); stroke-width: 3; }
  .edge-text {
    font-family: "Didact Gothic", sans-serif;
    font-size: 22px;
    letter-spacing: 2px;
    fill: var(--green);
    font-weight: 700;
  }
</style>
</head>
<body>
<svg class="sticker" viewBox="0 0 1200 1194" xmlns="http://www.w3.org/2000/svg" role="img" aria-label="Leaf-shaped green tea sticker for BrookLeafs">
  <defs>
    <path id="url-guide" class="guide" d="M432 830 C418 720 438 600 505 470"/>
    <path id="place-guide" class="guide" d="M690 915 C765 870 825 800 858 700"/>
  </defs>

  <g class="leaf">
    <path class="leaf-stem" d="M470 930 C430 990 380 1040 300 1080 L306 1092 C392 1054 446 1000 490 940 Z"/>
    <path class="leaf-body" d="M660 140
      C720 250 850 360 900 520
      C950 690 890 860 760 930
      C640 995 500 975 420 880
      C330 770 330 620 420 480
      C500 360 620 260 660 140 Z"/>
  </g>

  <text class="edge-text"><textPath href="#url-guide">www.brookleafs.co.uk</textPath></text>

  <g class="brand">
    <text class="brand-name" x="668" y="588" text-anchor="middle">BrookLeafs</text>
    <text class="brand-tagline" x="668" y="622" text-anchor="middle">Leaf Tea and Infusions</text>
  </g>

  <g class="tea-label">
    <line class="rule" x1="525" y1="652" x2="805" y2="652"/>
    <text class="tea-type" x="665" y="708" text-anchor="middle">green tea</text>
    <line class="rule" x1="525" y1="728" x2="805" y2="728"/>
  </g>

  <text class="edge-text"><textPath href="#place-guide">Welmoor, England</textPath></text>
</svg>
</body>
</html>
```